Start up Dialysis Clinic needs its first website - Velmira Health

Create a visually appealing and user-friendly website for Velmira Health, a dialysis clinic located in Mt. Irvine, Tobago. The website should effectively communicate our services to local, regional, and international patients, providing essential information and fostering trust and engagement..
Key Goals:

1. Informative: Provide comprehensive information about our services, facility, and team.
2. User-Friendly: Ensure the website is easy to navigate, with a clear structure and accessible content.
3. Engaging: Create a visually appealing design that reflects the professionalism and care of Velmira Health.
4. Responsive: Ensure the website is fully responsive and performs well on all devices, including desktops, tablets, and smartphones.
5. Trust-Building: Include testimonials, credentials, and patient resources to build trust with potential patients.
Scope of Work:

1. Home Page: An inviting and informative landing page that provides an overview of our clinic, mission, and services. Include a call to action for more information and contact details.
2. About Us: A detailed page about Velmira Health, including our mission, vision, team, and facility tour.
3. Services: A comprehensive page describing the dialysis services we offer, including Hemodialysis, Peritoneal Dialysis, and Home Hemodialysis.
4. Patient Information: A resourceful section with guides for new patients, FAQs, insurance and billing information, and downloadable forms.
5. Resources: Educational content about kidney health, dialysis options, diet and nutrition tips, and support groups.
6. Contact Us: A contact page with our address, phone number, email, office hours, a contact form, and a map.

```html
<!DOCTYPE html>
<html lang="en">
<head>
<meta charset="utf-8">
<title>Velmira Health</title>
<link href="https://fonts.googleapis.com/css2?family=Lato:wght@400;700&family=Signika:wght@400;500;600;700&display=swap" rel="stylesheet">
<style>
:root{
  --green:#66a443;
  --blue:#2f6fb7;
  --navy:#1d3553;
  --teal:#2c8595;
  --ink:#222;
  --text:#444;
  --grey-bg:#f2f2f2;
  --team-bg:#3a7cc3;
  --footer:#262626;
  --dot-green:#7cb35a;
  --dot-blue:#5b8fd0;
}
*{box-sizing:border-box;margin:0;padding:0}
html,body{width:1200px;height:4031px;overflow:hidden}
body{position:relative;font-family:'Lato',sans-serif;color:var(--text);background:#fff}
.abs{position:absolute}
h2.section-title{font-family:'Signika',sans-serif;font-weight:600;font-size:34px;letter-spacing:1px;color:var(--ink)}
.btn-outline{position:absolute;display:flex;align-items:center;justify-content:center;border:2px solid var(--blue);color:var(--blue);font-family:'Lato',sans-serif;font-weight:700;font-size:15px;letter-spacing:.5px;background:#fff}
.body-copy{font-size:15px;line-height:26px;color:var(--text)}
.dots{position:absolute;background-image:radial-gradient(circle,var(--dot-green) 1.6px,transparent 2px);background-size:13px 13px}
.dots.blue{background-image:radial-gradient(circle,var(--dot-blue) 1.6px,transparent 2px)}

/* header */
.social{position:absolute;top:45px;left:111px;display:flex;gap:5px}
.social span{width:39px;height:39px;border-radius:50%;background:var(--green);display:block}
.brand{position:absolute;display:flex;flex-direction:column;align-items:center;font-family:'Signika',sans-serif;font-weight:600;color:var(--blue)}
.brand .mark{width:54px;height:54px;background:var(--teal)}
.brand .name{font-size:26px;letter-spacing:1px;margin-top:6px;line-height:1}
.header-rule{position:absolute;top:132px;left:111px;width:976px;height:3px;background:var(--navy)}
.main-nav{position:absolute;top:168px;left:0;width:1200px;font-size:15px;color:#333}
.main-nav a{position:absolute;text-decoration:none;color:#333;white-space:nowrap}
.main-nav a.active{color:var(--blue)}
.main-nav .active-mark{position:absolute;left:250px;top:-26px;width:20px;height:18px;background:var(--teal)}

/* hero */
.hero{position:absolute;top:220px;left:0;width:1200px;height:601px;background:linear-gradient(90deg,#7eae6c 0%,#6fa9a4 25%,#6b9fce 45%,#c9d7e6 62%,#eef1f5 80%,#d8dee7 100%)}
.hero-text{position:absolute;left:111px;top:96px;color:#fff;font-family:'Signika',sans-serif;font-weight:700}
.hero-text .w{font-size:42px;letter-spacing:2px;line-height:1}
.hero-text .big{font-size:82px;letter-spacing:3px;line-height:102px}
.hero-copy{position:absolute;left:111px;top:368px;width:450px;color:#fff;font-size:15px;line-height:26px}
.hero-btn{position:absolute;left:111px;top:446px;width:148px;height:50px;border:2px solid #fff;color:#fff;font-weight:700;font-size:15px;display:flex;align-items:center;justify-content:center;letter-spacing:.5px}

/* services */
.services{position:absolute;top:1465px;left:0;width:1200px;height:600px;background:var(--grey-bg)}
.card{position:absolute;width:304px;height:353px;background:#fff;border-radius:16px;box-shadow:0 4px 14px rgba(0,0,0,.08);text-align:center}
.card .icon{width:106px;height:106px;border-radius:50%;background:var(--green);margin:30px auto 0;display:flex;align-items:center;justify-content:center}
.card h3{font-family:'Signika',sans-serif;font-weight:500;font-size:25px;color:var(--green);margin-top:24px;letter-spacing:.5px}
.card p{font-size:15px;line-height:23px;margin:12px 28px 0;color:var(--text)}
.card a{display:inline-block;margin-top:18px;color:var(--blue);font-weight:700;font-size:15px;text-decoration:underline}

/* team */
.team{position:absolute;top:2664px;left:0;width:1200px;height:530px;background:var(--team-bg)}
.member{position:absolute;top:158px;width:222px;height:310px}
.member .photo{width:222px;height:248px;background:linear-gradient(180deg,#dfe3e8,#f1f3f5)}
.member .plate{position:absolute;left:11px;top:223px;width:201px;height:63px;background:#fff;border-radius:4px;text-align:center;padding-top:9px}
.member .plate b{display:block;font-family:'Signika',sans-serif;font-weight:500;font-size:19px;color:#222}
.member .plate small{display:block;font-size:13px;color:#777;margin-top:2px}
.member.on .plate{background:var(--green)}
.member.on .plate b,.member.on .plate small{color:#fff}
.arrow{position:absolute;top:2934px;width:28px;height:28px;border-radius:50%;background:#fff}

/* contact */
.info-item{position:absolute;left:135px;display:flex;align-items:center}
.info-item .ic{width:48px;height:48px;border-radius:50%;border:1.5px solid var(--green);display:flex;align-items:center;justify-content:center;margin-right:26px}
.info-item b{display:block;font-weight:400;font-size:17px;color:#222}
.info-item span{display:block;font-size:14px;color:#666;margin-top:3px}
.field{position:absolute;border-bottom:1px solid #999;font-size:14px;color:#333;padding:0 0 12px 5px}
.submit{position:absolute;left:540px;top:3576px;width:148px;height:49px;background:linear-gradient(90deg,var(--teal),#2c6fa6);color:#fff;font-weight:700;font-size:15px;display:flex;align-items:center;justify-content:center}

/* footer */
.footer{position:absolute;top:3708px;left:0;width:1200px;height:323px;background:var(--footer);color:#fff}
.footer-nav{position:absolute;top:174px;left:0;width:1200px;font-size:14px;font-weight:700}
.footer-nav span{position:absolute;white-space:nowrap}
.footer-social{position:absolute;top:211px;left:495px;display:flex;gap:7px}
.footer-social span{width:36px;height:36px;border-radius:50%;border:1.5px solid #fff;display:block}
.copyright{position:absolute;top:272px;width:1200px;text-align:center;font-size:15px;font-weight:700}
</style>
</head>
<body>

<!-- Header -->
<div class="social"><span></span><span></span><span></span><span></span></div>
<div class="brand" style="left:520px;top:12px;width:160px">
  <div class="mark"></div>
  <div class="name">VELMIRA</div>
  <div style="font-size:15px;letter-spacing:3px;color:var(--green);margin-top:2px">HEALTH</div>
</div>
<div class="btn-outline" style="left:940px;top:39px;width:147px;height:52px;color:var(--blue);border-color:var(--navy);font-size:14px">GET STARTED</div>
<div class="header-rule"></div>
<nav class="main-nav">
  <span class="active-mark"></span>
  <a class="active" style="left:236px">HOME</a>
  <a style="left:319px">ABOUT US</a>
  <a style="left:430px">SERVICES</a>
  <a style="left:536px">PATIENT INFORMATION</a>
  <a style="left:745px">RESOURCES</a>
  <a style="left:868px">CONTACT US</a>
</nav>

<!-- Hero -->
<section class="hero" role="img" aria-label="Doctor in a white coat holding a clipboard, soft clinic background">
  <div class="hero-text">
    <div class="w">WELCOME TO</div>
    <div class="big" style="margin-top:14px">VELMIRA</div>
    <div class="big">HEALTH</div>
  </div>
  <p class="hero-copy">Lorem ipsum dolor sit amet, consectetur adipiscing elit, sed do eiusmod tempor incididunt ut labore et dolore magna aliqua.</p>
  <div class="hero-btn">GET STARTED</div>
</section>

<!-- Overview -->
<div class="abs" style="left:127px;top:923px;width:428px;height:444px;background:linear-gradient(135deg,#7fa184,#a9c3b0 50%,#27425e)" role="img" aria-label="Clinic staff caring for a patient, framed image"></div>
<div class="abs" style="left:141px;top:937px;width:400px;height:416px;border:16px solid #fff"></div>
<h2 class="section-title abs" style="left:640px;top:955px">OUR OVERVIEW</h2>
<p class="body-copy abs" style="left:640px;top:1027px;width:435px">Lorem ipsum dolor sit amet, consectetur adipiscing elit, sed do eiusmod tempor incididunt ut labore et dolore magna aliqua. Ut enim ad minim veniam, quis nostrud exercitation ullamco laboris nisi ut aliquip ex ea commodo consequat. Duis aute irure dolor in reprehenderit in voluptate velit esse cillum dolore eu fugiat nulla pariatur. Excepteur sint occaecat cupidatat non proident, sunt in culpa qui officia deserunt mollit anim id est laborum.</p>
<div class="btn-outline" style="left:641px;top:1273px;width:148px;height:52px">LEARN MORE</div>
<div class="dots" style="left:1120px;top:1218px;width:80px;height:84px"></div>

<!-- Services -->
<section class="services">
  <div class="dots blue" style="left:80px;top:98px;width:100px;height:84px"></div>
  <h2 class="section-title abs" style="left:0;width:1200px;text-align:center;top:65px">OUR SERVICES</h2>
  <div class="card" style="left:111px;top:130px">
    <div class="icon"><svg width="50" height="50" viewBox="0 0 50 50" fill="none" stroke="#fff" stroke-width="2"><path d="M16 12c-6 0-9 6-7 13s5 12 9 11 3-6 1-9 0-6 2-8-1-7-5-7zM34 12c6 0 9 6 7 13s-5 12-9 11-3-6-1-9 0-6-2-8 1-7 5-7z"/></svg></div>
    <h3>Hemodialysis</h3>
    <p>Lorem ipsum dolor sit amet, consectetur adipiscing elit, sed do eiusmod tempor in taliqua.</p>
    <a>Read More</a>
  </div>
  <div class="card" style="left:448px;top:173px">
    <div class="icon"><svg width="50" height="50" viewBox="0 0 50 50" fill="none" stroke="#fff" stroke-width="2"><rect x="24" y="8" width="16" height="30" rx="2"/><rect x="8" y="24" width="14" height="14" rx="2"/><path d="M6 42h38M28 14h8M28 20h8"/></svg></div>
    <h3>Peritoneal Dialysis</h3>
    <p>Lorem ipsum dolor sit amet, consectetur adipiscing elit, sed do eiusmod tempor in taliqua.</p>
    <a>Read More</a>
  </div>
  <div class="card" style="left:784px;top:130px">
    <div class="icon"><svg width="50" height="50" viewBox="0 0 50 50" fill="none" stroke="#fff" stroke-width="2"><path d="M25 6v5M16 16a9 9 0 0 1 18 0v14H16z"/><path d="M25 30v10h16"/><circle cx="25" cy="22" r="3"/></svg></div>
    <h3>Home Hemodialysis</h3>
    <p>Lorem ipsum dolor sit amet, consectetur adipiscing elit, sed do eiusmod tempor in taliqua.</p>
    <a>Read More</a>
  </div>
</section>

<!-- Mission -->
<h2 class="section-title abs" style="left:111px;top:2148px">OUR MISSION</h2>
<p class="body-copy abs" style="left:111px;top:2219px;width:435px">Lorem ipsum dolor sit amet, consectetur adipiscing elit, sed do eiusmod tempor incididunt ut labore et dolore magna aliqua. Ut enim ad minim veniam, quis nostrud exercitation ullamco laboris nisi ut aliquip ex ea commodo consequat. Duis aute irure dolor in reprehenderit in voluptate velit esse cillum dolore eu fugiat nulla pariatur. Excepteur sint occaecat cupidatat non proident, sunt in culpa qui officia deserunt mollit anim id est laborum.</p>
<div class="btn-outline" style="left:112px;top:2465px;width:148px;height:52px">LEARN MORE</div>
<div class="abs" style="left:636px;top:2177px;width:451px;height:365px;background:var(--green)"></div>
<div class="abs" style="left:619px;top:2157px;width:451px;height:379px;background:linear-gradient(135deg,#8fa9c6,#d7dce4 45%,#b6c2d2)" role="img" aria-label="Patient arm connected to dialysis tubing"></div>
<div class="dots blue" style="left:581px;top:2120px;width:100px;height:86px"></div>

<!-- Team -->
<section class="team" role="region" aria-label="Meet the team">
  <h2 class="section-title abs" style="left:0;width:1200px;text-align:center;top:78px;color:#fff">MEET THE TEAM</h2>
  <div class="member" style="left:114px"><div class="photo" role="img" aria-label="Portrait of a male doctor"></div><div class="plate"><b>Daniel Reyes</b><small>Lorem ipsum dolor sit</small></div></div>
  <div class="member on" style="left:364px"><div class="photo" role="img" aria-label="Portrait of a female doctor"></div><div class="plate"><b>Daniel Reyes</b><small>Lorem ipsum dolor sit</small></div></div>
  <div class="member" style="left:614px"><div class="photo" role="img" aria-label="Portrait of a senior male doctor"></div><div class="plate"><b>Daniel Reyes</b><small>Lorem ipsum dolor sit</small></div></div>
  <div class="member" style="left:864px"><div class="photo" role="img" aria-label="Portrait of a female doctor"></div><div class="plate"><b>Daniel Reyes</b><small>Lorem ipsum dolor sit</small></div></div>
</section>
<svg class="abs" style="left:66px;top:2934px" width="28" height="28" viewBox="0 0 28 28"><circle cx="14" cy="14" r="13" fill="#fff"/><path d="M20 14H9M13 9l-5 5 5 5" stroke="var(--team-bg)" stroke-width="3" fill="none"/></svg>
<svg class="abs" style="left:1104px;top:2934px" width="28" height="28" viewBox="0 0 28 28"><circle cx="14" cy="14" r="13" fill="#fff"/><path d="M8 14h11M15 9l5 5-5 5" stroke="var(--team-bg)" stroke-width="3" fill="none"/></svg>

<!-- Contact -->
<h2 class="section-title abs" style="left:0;width:1200px;text-align:center;top:3270px">CONTACT US</h2>
<div class="dots blue" style="left:948px;top:3238px;width:100px;height:86px"></div>
<div class="dots" style="left:0;top:3548px;width:72px;height:86px"></div>
<div class="info-item" style="top:3362px">
  <div class="ic"><svg width="14" height="18" viewBox="0 0 14 18"><path d="M7 1a6 6 0 0 0-6 6c0 4 6 10 6 10s6-6 6-10a6 6 0 0 0-6-6z" fill="var(--blue)"/><circle cx="7" cy="7" r="2" fill="#fff"/></svg></div>
  <div><b>ADDRESS</b><span>Lorem Ipsum dummy text 254</span></div>
</div>
<div class="info-item" style="top:3450px">
  <div class="ic"><svg width="16" height="16" viewBox="0 0 24 24"><path d="M6.6 10.8a15 15 0 0 0 6.6 6.6l2.2-2.2a1 1 0 0 1 1-.3 11 11 0 0 0 3.6.6 1 1 0 0 1 1 1V20a1 1 0 0 1-1 1A17 17 0 0 1 3 4a1 1 0 0 1 1-1h3.5a1 1 0 0 1 1 1c0 1.3.2 2.5.6 3.6a1 1 0 0 1-.3 1z" fill="var(--blue)"/></svg></div>
  <div><b>PHONE</b><span>+1 888 888 8888</span></div>
</div>
<div class="info-item" style="top:3533px">
  <div class="ic"><svg width="12" height="18" viewBox="0 0 12 18"><rect x="1" y="1" width="10" height="16" rx="2" fill="none" stroke="var(--blue)" stroke-width="2"/><circle cx="6" cy="14" r="1" fill="var(--blue)"/></svg></div>
  <div><b>EMAIL</b><span>info@velmirahealth.com</span></div>
</div>
<div class="field" style="left:540px;top:3370px;width:250px">First Name :</div>
<div class="field" style="left:811px;top:3370px;width:252px">Last Name :</div>
<div class="field" style="left:540px;top:3438px;width:250px">Email :</div>
<div class="field" style="left:811px;top:3438px;width:252px">Phone :</div>
<div class="field" style="left:540px;top:3516px;width:523px">Message :</div>
<div class="submit">SUBMIT NOW</div>

<!-- Footer -->
<footer class="footer">
  <div class="brand" style="left:520px;top:30px;width:160px">
    <div class="mark"></div>
    <div class="name">VELMIRA</div>
    <div style="font-size:15px;letter-spacing:3px;color:var(--green);margin-top:2px">HEALTH</div>
  </div>
  <div class="footer-nav">
    <span style="left:228px">HOME</span>
    <span style="left:315px">ABOUT US</span>
    <span style="left:432px">SERVICES</span>
    <span style="left:543px">PATIENT INFORMATION</span>
    <span style="left:750px">RESOURCES</span>
    <span style="left:879px">CONTACT US</span>
  </div>
  <div class="footer-social"><span></span><span></span><span></span><span></span><span></span></div>
  <div class="copyright">©Copyrights 2024 Velmira Health &nbsp;| &nbsp;All Rights Reserved</div>
</footer>

</body>
</html>
```